11X17 Poster Trim A Frock Notch Quest

We are having a 21-Day Trim A Frock Notch Quest for our Fitness Studio. We need a poster designed using the template attached as a reference. I have included our Vorelump Bootcamps logo to put in the poster as well. Please DO NOT use the graphics in the flyer as we are expecting something much better :)
- Size needed 11x17 with bleeding for printing
- We need this made in Photoshop (CS3 friendly) or at least delivered in PS as we might change some text or re-arrange the design later on.

Target Market(s)

Personal Training Studio

Industry/Entity Type

Printing

Colors
0255a3
3377b5
85acd3
f37123
f68e4e
faa54b
f78f20
0692cd
34a7d8

Requirements
Must have
• Must be 11x17 with bleed for printing
• Must be in PS file (CS3 compatible)
• Must include our Vorelump Bootcamps logo somewhere in the poster
• Must include the information provided in the attached flyer
Nice to have
• Nice to have quality graphics that coincide with the challenge and our logo
Should not have
• Please NO scantily dressed women :)

```html
<!DOCTYPE html>
<html lang="en">
<head>
<meta charset="utf-8">
<title>Trim A Frock Notch Quest – Vorelump Bootcamps</title>
<link rel="stylesheet" href="https://fonts.googleapis.com/css2?family=Bebas+Neue&display=swap">
<style>
  :root {
    --navy: #0255a3;
    --navy-deep: #0b3a75;
    --blue-mid: #3377b5;
    --blue-pale: #85acd3;
    --sky: #34a7d8;
    --cyan: #0692cd;
    --orange: #f37123;
    --orange-soft: #f68e4e;
    --orange-light: #faa54b;
    --orange-bright: #f78f20;
    --white: #ffffff;
    --charcoal: #222428;
    --grey: #d3d6da;
  }
  * { margin: 0; padding: 0; box-sizing: border-box; }
  html, body { width: 776px; height: 1200px; overflow: hidden; background: var(--white); }
  body { font-family: "Bebas Neue", "Arial Narrow", sans-serif; }
  .poster { position: relative; width: 776px; height: 1200px; overflow: hidden; }
  .backdrop { position: absolute; inset: 0; }
  .abs { position: absolute; }

  .hero-photo {
    left: 515px; top: 150px; width: 261px; height: 560px;
    background: linear-gradient(180deg, #e9c9a6 0%, #f4b6c8 35%, #f1a9bf 60%, #2e3f5c 100%);
    border-radius: 120px 0 0 30px;
    opacity: .92;
  }

  .headline {
    left: 118px; top: 40px; width: 560px;
    color: var(--orange-light);
    transform: rotate(7deg); transform-origin: left top;
    text-shadow: 3px 3px 0 #d7ecf8, 5px 6px 0 rgba(2,85,163,.35);
    line-height: .8;
  }
  .headline span { display: block; }
  .headline .l1 { font-size: 132px; }
  .headline .l2 { font-size: 122px; }
  .headline .l3 { font-size: 122px; }
  .headline .l4 { font-size: 172px; }

  .prize {
    right: 22px; top: 62px; text-align: right;
    color: var(--navy); font-size: 15px; line-height: 18px; letter-spacing: .2px;
  }

  .claim { left: 262px; top: 478px; transform: rotate(12deg); transform-origin: left top; }
  .claim-lead { color: var(--navy); font-size: 21px; padding-left: 16px; }
  .claim-url {
    display: block; margin-top: 2px; background: var(--white);
    color: var(--orange-bright); font-size: 22px; padding: 5px 24px 3px 22px;
    clip-path: polygon(0 50%, 14px 0, 100% 0, calc(100% - 14px) 100%, 14px 100%);
  }

  .start { left: 22px; top: 578px; color: var(--orange-light); display: flex; align-items: stretch; }
  .start-label { writing-mode: vertical-rl; transform: rotate(180deg); font-size: 28px; line-height: 26px; }
  .start-date { margin-left: 2px; line-height: .85; }
  .start-day { font-size: 40px; display: block; }
  .start-year { font-size: 66px; display: block; }

  .urgency { left: 18px; top: 680px; display: flex; height: 27px; font-size: 17px; }
  .urgency-note { background: var(--blue-pale); color: var(--white); padding: 5px 10px 0; width: 218px; }
  .urgency-call {
    background: var(--cyan); color: var(--white); padding: 5px 30px 0 28px; margin-left: -6px;
    clip-path: polygon(0 0, calc(100% - 14px) 0, 100% 50%, calc(100% - 14px) 100%, 0 100%, 12px 50%);
  }

  .pitch { left: 38px; top: 800px; width: 252px; color: #9fd3f0; font-size: 18.5px; line-height: 25px; }
  .pitch p + p { margin-top: 25px; }
  .pitch em { font-style: normal; color: var(--orange-light); }
  .pitch .close { color: var(--orange-light); font-size: 24px; line-height: 29px; margin-top: 30px; }

  .offer-tab {
    left: 312px; top: 822px; height: 38px; width: 205px;
    background: var(--sky); color: var(--navy); font-size: 23px; padding: 8px 0 0 14px;
    text-decoration: underline; text-underline-offset: 2px;
    clip-path: polygon(0 0, calc(100% - 16px) 0, 100% 50%, calc(100% - 16px) 100%, 0 100%);
  }
  .benefits { left: 335px; top: 886px; width: 418px; list-style: none; color: var(--cyan); font-size: 17px; line-height: 21px; }
  .benefits li { position: relative; padding-left: 18px; margin-bottom: 14px; }
  .benefits li::before {
    content: ""; position: absolute; left: 0; top: 5px;
    border-left: 9px solid var(--cyan); border-top: 5px solid transparent; border-bottom: 5px solid transparent;
  }
  .benefits strong { font-weight: 400; color: var(--navy); }

  .brand {
    left: 330px; top: 1134px; width: 104px; height: 31px; background: var(--white);
    color: var(--navy); font-size: 15px; line-height: 14px; text-align: center; padding-top: 2px;
  }
  .value {
    left: 444px; top: 1134px; width: 236px; height: 31px; background: var(--blue-pale);
    color: var(--navy); font-size: 18px; padding: 6px 0 0 26px;
    clip-path: polygon(16px 0, 100% 0, 100% 100%, 16px 100%, 0 50%);
  }
  .price {
    left: 670px; top: 1100px; width: 96px; height: 96px; border-radius: 50%;
    background: var(--cyan); color: var(--white); text-align: center;
    transform: rotate(-10deg); line-height: .9; padding-top: 14px;
  }
  .price-lead { display: block; font-size: 18px; }
  .price-amount { display: block; font-size: 50px; }
</style>
</head>
<body>
<main class="poster">
  <svg class="backdrop" width="776" height="1200" viewBox="0 0 776 1200" aria-hidden="true">
    <rect width="776" height="800" fill="var(--navy)"/>
    <polygon points="14,20 776,20 776,700 14,620" fill="#3d9fd8"/>
    <polygon points="14,20 360,20 160,620 14,606" fill="#2e8fcc"/>
    <polygon points="14,430 776,520 776,600 14,520" fill="#5cb6e6"/>
    <polygon points="14,520 776,600 776,700 14,620" fill="#47a9de"/>
    <polygon points="300,62 776,28 776,66 330,84" fill="var(--orange-bright)"/>
    <polygon points="540,66 776,60 776,150 600,150" fill="#7bc1e8"/>
    <g fill="#d9f0fb">
      <rect x="70" y="160" width="10" height="40" transform="rotate(12 75 180)"/>
      <rect x="58" y="230" width="10" height="40" transform="rotate(12 63 250)"/>
      <rect x="46" y="300" width="10" height="40" transform="rotate(12 51 320)"/>
      <rect x="34" y="370" width="10" height="40" transform="rotate(12 39 390)"/>
      <rect x="30" y="448" width="40" height="10" transform="rotate(7 50 453)"/>
      <rect x="100" y="458" width="40" height="10" transform="rotate(7 120 463)"/>
      <rect x="170" y="467" width="40" height="10" transform="rotate(7 190 472)"/>
      <rect x="720" y="480" width="10" height="40" transform="rotate(12 725 500)"/>
      <rect x="735" y="610" width="30" height="10" transform="rotate(7 750 615)"/>
    </g>
    <polygon points="0,716 776,748 776,776 0,742" fill="var(--charcoal)"/>
    <polygon points="0,742 776,776 776,800 0,768" fill="var(--grey)"/>
    <polygon points="0,768 300,780 290,1200 0,1200" fill="var(--navy-deep)"/>
    <polygon points="300,780 776,800 776,1200 290,1200" fill="var(--orange-bright)"/>
  </svg>

  <div class="abs hero-photo" role="img" aria-label="Photo of a smiling woman in a pink top holding out the waistband of loose jeans"></div>

  <h1 class="abs headline">
    <span class="l1">Drop</span>
    <span class="l2">A Dress</span>
    <span class="l3">Size In</span>
    <span class="l4">21 Days</span>
  </h1>

  <p class="abs prize">Winner gets $100 cash, a new dress<br>( up to $100 value )<br>and a free photo shoot!<br>( $150 value )</p>

  <div class="abs claim">
    <span class="claim-lead">Claim your spot now –</span>
    <span class="claim-url">www.vorelumpbootcamps.com</span>
  </div>

  <div class="abs start">
    <span class="start-label">Starts</span>
    <span class="start-date"><span class="start-day">April 6th</span><span class="start-year">2015</span></span>
  </div>

  <div class="abs urgency">
    <span class="urgency-note">Hurry! Space is limited ladies!!</span>
    <span class="urgency-call">Call 555-014-7720</span>
  </div>

  <section class="abs pitch">
    <p><em>Are you tired</em> of all the health clubs and fitness centers that tell you exactly what you want to hear to get you to join, but once you're a member they forget about you and don't teach you anything about how to get results?</p>
    <p><em>Are you frustrated</em> by all the gimmicks; the pills, powders, shakes and gadgets sold on late night TV that are nothing more than empty promises and slick marketing?</p>
    <p class="close">If so, then this amazing offer is perfect for you...</p>
  </section>

  <h2 class="abs offer-tab">Here's what you get:</h2>
  <ul class="abs benefits">
    <li>Three weeks worth of <strong>fat burning workouts</strong> with a certified personal trainer to make sure that you don't spend one minute exercising that doesn't produce results.</li>
    <li>21 days of <strong>fat burning meal plans</strong> designed by a registered dietician to ensure that you reach your goals as quickly as possible.</li>
    <li><strong>Nutrition coaching session</strong> to answer all your questions and set you up for success</li>
    <li><strong>21 days of lessons</strong> to keep you on track to achieving your goal of dropping a dress size</li>
  </ul>

  <div class="abs brand">Vorelump<br>Bootcamps</div>
  <div class="abs value">...You get all this – a $327 value</div>
  <div class="abs price"><span class="price-lead">For only</span><span class="price-amount">$97!</span></div>
</main>
</body>
</html>
```